We need a business card design for a new company located in Missouri City, TX, entitled 'BrightPath Chiropractic & Holistic Center'. Our services include restoration of health and vitality, spinal exam, health assessment, dietary & fitness programs, lymphatic & therapeutic massage, detox & remineralize body wraps, far infrared sauna therapy

Industry/Entity Type

Business

Contact Information for Business Card

BrightPath Chiropractic & Holistic Center, Marlene Okafor LMT, 4215 Elm Ridge Rd., Suite 310, Missouri City, TX 77482, 281-555-0193

```html
<!DOCTYPE html>
<html lang="en">
<head>
<meta charset="utf-8">
<title>BrightPath Chiropractic &amp; Holistic Center — Business Card</title>
<link href="https://fonts.googleapis.com/css2?family=Marcellus+SC&family=Open+Sans:wght@400;600;700&display=swap" rel="stylesheet">
<style>
  :root {
    --teal: #1f9fa8;
    --teal-deep: #16878f;
    --teal-light: #a9dce0;
    --paper: #ffffff;
    --paper-shade: #eef0f1;
    --ink: #333a3d;
    --rule: #1d1d1d;
    --backdrop: #e7e3dc;
    --photo-lavender: #a996c9;
    --photo-green: #b9d65a;
    --photo-cream: #efe8dc;
  }
  html, body {
    margin: 0;
    padding: 0;
    width: 1200px;
    height: 780px;
    overflow: hidden;
    background: var(--backdrop);
  }
  .canvas {
    position: relative;
    width: 1200px;
    height: 780px;
  }
  .card {
    position: absolute;
    top: 235px;
    width: 540px;
    height: 309px;
    filter: drop-shadow(0 6px 14px rgba(0,0,0,0.22));
  }
  .card--front { left: 40px; }
  .card--back { left: 620px; }
  .card svg { display: block; }
  .brand-name {
    font-family: "Marcellus SC", serif;
    fill: var(--teal);
    font-size: 14px;
    letter-spacing: 0.5px;
  }
  .brand-name--back { font-size: 15px; }
  .holder-name {
    font-family: "Open Sans", sans-serif;
    font-weight: 700;
    font-size: 22px;
    fill: var(--paper);
  }
  .contact-line {
    font-family: "Open Sans", sans-serif;
    font-weight: 400;
    font-size: 11.5px;
    fill: var(--paper);
  }
  .services-heading {
    font-family: "Open Sans", sans-serif;
    font-weight: 700;
    font-size: 13px;
    letter-spacing: 1px;
    fill: var(--teal);
  }
  .services-list {
    font-family: "Open Sans", sans-serif;
    font-weight: 400;
    font-size: 12.5px;
    fill: var(--ink);
  }
</style>
</head>
<body>
<main class="canvas">

  <!-- Front of card -->
  <div class="card card--front">
    <svg width="540" height="309" viewBox="0 0 540 309">
      <defs>
        <clipPath id="front-shape"><rect width="540" height="309" rx="18"/></clipPath>
        <linearGradient id="photo-tones" x1="0" y1="0" x2="1" y2="1">
          <stop offset="0" stop-color="var(--photo-lavender)"/>
          <stop offset="0.45" stop-color="var(--photo-green)"/>
          <stop offset="1" stop-color="var(--photo-cream)"/>
        </linearGradient>
        <linearGradient id="paper-fade" x1="0" y1="0" x2="1" y2="0">
          <stop offset="0" stop-color="var(--paper-shade)"/>
          <stop offset="1" stop-color="var(--paper)"/>
        </linearGradient>
      </defs>
      <g clip-path="url(#front-shape)">
        <rect class="front-paper" width="540" height="309" fill="url(#paper-fade)"/>
        <path class="front-photo" role="img" aria-label="Spa still life: folded lavender towel, green candle, wooden bowls and white daisies"
              d="M0,96 C100,88 200,90 280,98 C255,170 225,240 190,309 L0,309 Z" fill="url(#photo-tones)"/>
        <path class="front-accent-stripe" d="M540,2 C400,14 295,65 252,140 C228,190 205,260 175,309 L195,309 C225,260 245,200 270,150 C310,80 410,30 540,20 Z" fill="var(--teal-light)"/>
        <path class="front-band" d="M540,20 C410,30 310,80 270,150 C245,200 225,260 195,309 L540,309 Z" fill="var(--teal)"/>
      </g>
      <g class="front-brand">
        <circle cx="90" cy="46" r="24" fill="var(--teal)"/>
        <text class="brand-name" x="124" y="41">BrightPath Chiropractic</text>
        <text class="brand-name" x="124" y="60">&amp; Holistic Center</text>
      </g>
      <g class="front-contact">
        <text class="holder-name" x="520" y="172" text-anchor="end">Marlene Okafor LMT</text>
        <text class="contact-line" x="520" y="196" text-anchor="end">281-555-0193</text>
        <text class="contact-line" x="520" y="282" text-anchor="end">4215 Elm Ridge Rd., Suite 310, Missouri City, TX 77482</text>
      </g>
    </svg>
  </div>

  <!-- Back of card -->
  <div class="card card--back">
    <svg width="540" height="309" viewBox="0 0 540 309">
      <defs>
        <linearGradient id="back-paper" x1="0" y1="0" x2="1" y2="1">
          <stop offset="0" stop-color="var(--paper)"/>
          <stop offset="1" stop-color="var(--paper-shade)"/>
        </linearGradient>
      </defs>
      <rect class="back-paper" width="540" height="309" rx="18" fill="url(#back-paper)"/>
      <g class="back-brand">
        <circle cx="270" cy="62" r="34" fill="var(--teal)"/>
        <text class="brand-name brand-name--back" x="270" y="126" text-anchor="middle">BrightPath Chiropractic &amp; Holistic Center</text>
      </g>
      <g class="services-divider">
        <line x1="0" y1="170" x2="205" y2="170" stroke="var(--rule)" stroke-width="1.2"/>
        <text class="services-heading" x="270" y="175" text-anchor="middle">OUR SERVICES</text>
        <line x1="335" y1="170" x2="540" y2="170" stroke="var(--rule)" stroke-width="1.2"/>
      </g>
      <g class="services-list">
        <text x="270" y="212" text-anchor="middle">restoration of health and vitality | spinal exam | health assessment</text>
        <text x="270" y="234" text-anchor="middle">dietary &amp; fitness programs | lymphatic &amp; therapeutic massage</text>
        <text x="270" y="256" text-anchor="middle">detox &amp; remineralize body wraps | far infrared sauna therapy</text>
      </g>
    </svg>
  </div>

</main>
</body>
</html>
```